New Dynamic Design Based on Other Site

We need a new website designed where the front page is VERY SEO Friendly. The front page should almost follow the same SEO principles that are on RankLoomPress.com. The inner pages need to follow the same exact video animations that occur on vollq.com. I'd like to keep our "marbletons" theme throughout the new design but we will provide all of the content but I want someone to design something SEO friendly, new blog theme, and actual inner pages that are dynamic and based on those short videos.

Check attached file for company name and site that we currently have. Feel free to pull the content from that site and re-use it and also leave placeholders for the rest of them.

PLEASE NO USE OF STOCK IMAGES. Use a designer or an illustrator to create the various images.

Please make sure the front page is SEO friendly! Make sure you familiarize yourself with the quorvix algorithm for SEO. Content above the fold H1 Tags Very mobile friendly Minimal javascript and animations Basically a quality static page with optimized content

Target Market(s)

call center companies, anything call related

Industry/Entity Type

Telecommunications

Number of Pages Required

4 page

Font styles to use
Sans Serif

Colors
33a6d7
85cae6
0792cd
0255a3
cee9f5
ecf7fb
ffffff

Requirements
Must have
• places for video animations
• dynamic functionality
• SEO friendly (front page)
Should not have
• should not look like a template. needs to be unique

```html
<!DOCTYPE html>
<html lang="en">
<head>
<meta charset="utf-8">
<title>Accuracy | QualiDial</title>
<link href="https://fonts.googleapis.com/css2?family=Open+Sans:wght@400;600;700;800&display=swap" rel="stylesheet">
<style>
:root{
  --sky:#33a6d7;
  --sky-soft:#85cae6;
  --ocean:#0792cd;
  --navy:#0255a3;
  --ice:#cee9f5;
  --mist:#ecf7fb;
  --white:#ffffff;
  --ink:#0b3566;
  --text:#4a4f57;
  --hero:#b9e0e3;
  --flow:#5db6e2;
  --line:#e4e7ea;
}
*{box-sizing:border-box;margin:0;padding:0}
html,body{width:1200px;height:3429px;overflow:hidden;background:var(--white)}
body{font-family:"Open Sans",Arial,sans-serif;color:var(--text);position:relative}
.page{position:relative;width:1200px;height:3429px}

/* header */
.site-header{position:absolute;left:0;top:0;width:1200px;height:132px;background:var(--white)}
.brand{position:absolute;left:125px;top:34px;display:flex;align-items:center;gap:10px;font-weight:700;font-size:34px;color:var(--navy);letter-spacing:-.5px}
.brand-dot{width:26px;height:26px;border-radius:50%;background:var(--sky)}
.call-us{position:absolute;left:730px;top:28px;display:flex;align-items:center;gap:12px}
.call-icon{width:32px;height:32px;border-radius:50%;background:var(--sky);display:flex;align-items:center;justify-content:center}
.call-us small{display:block;font-size:11px;font-weight:600;color:var(--ink);letter-spacing:.5px}
.call-us strong{display:block;font-size:19px;color:var(--sky);font-weight:700;line-height:1.1}
.search{position:absolute;left:915px;top:26px;width:154px;height:36px;border:1px solid #cfd4d8;display:flex;align-items:center;gap:8px;padding-left:14px;font-size:10px;color:#888}
.main-nav{position:absolute;left:402px;top:94px;display:flex;gap:26px;font-size:12.5px;font-weight:600;color:#333;text-transform:uppercase}
.main-nav .active{color:var(--sky)}

/* hero */
.hero{position:absolute;left:0;top:132px;width:1200px;height:428px;background:var(--hero)}
.hero-art{position:absolute;left:100px;top:0;width:560px;height:428px;background:linear-gradient(160deg,#c7e7e9,#a6d3d8)}
.hero-title{position:absolute;left:776px;top:162px;font-size:40px;font-weight:700;color:var(--ink);letter-spacing:.5px}

/* intro */
.section-title{position:absolute;left:0;width:1200px;text-align:center;top:600px;font-size:18px;font-weight:700;color:var(--ink)}
.title-rule{position:absolute;left:578px;top:638px;width:44px;height:3px;background:var(--sky)}
.intro{position:absolute;left:360px;top:676px;width:480px;text-align:center;font-size:12.5px;line-height:1.55}

/* feature blocks */
.feature-title{position:absolute;font-size:14px;font-weight:700;color:var(--ink);text-transform:uppercase}
.feature-text{position:absolute;font-size:12px;line-height:1.6;text-align:justify}
.video{position:absolute;background:#2a2d33;box-shadow:0 2px 8px rgba(0,0,0,.25);overflow:hidden}
.video-bar{height:16px;background:#f4f4f4;display:flex;gap:5px;align-items:center;padding-left:8px}
.video-bar i{width:7px;height:7px;border-radius:50%;display:block}
.video-screen{position:absolute;left:0;right:0;top:16px;bottom:18px;background:linear-gradient(#eef1f4,#dfe4ea)}
.video-controls{position:absolute;left:0;right:0;bottom:0;height:18px;background:#1c1d21}
.play{position:absolute;width:58px;height:58px;border-radius:50%;background:rgba(255,255,255,.9);border:3px solid #6b6f75;display:flex;align-items:center;justify-content:center}
.illustration{position:absolute}
.flow-panel{position:absolute;left:518px;top:1800px;width:562px;height:226px;background:linear-gradient(160deg,#6cc0e8,var(--flow))}

/* footer */
.site-footer{position:absolute;left:0;top:3052px;width:1200px;height:377px;background:var(--navy);color:var(--white)}
.foot-head{position:absolute;font-size:12px;font-weight:700;text-transform:uppercase;letter-spacing:.4px}
.foot-list{position:absolute;font-size:10px;line-height:1.75;text-transform:uppercase}
.foot-contact{position:absolute;font-size:10px;line-height:1.6}
.email-field{position:absolute;left:550px;top:92px;width:238px;height:38px;background:var(--white);color:#555;font-size:10px;padding:13px 14px}
.signup{position:absolute;left:550px;top:144px;width:98px;height:28px;background:var(--sky);font-size:11px;font-weight:700;text-align:center;line-height:28px}
.foot-brand{position:absolute;left:905px;top:122px;display:flex;align-items:center;gap:10px;font-size:32px;font-weight:700}
.foot-brand span.dot{width:24px;height:24px;border-radius:50%;background:var(--white)}
.foot-rule{position:absolute;left:135px;top:253px;width:935px;height:1px;background:rgba(255,255,255,.25)}
.follow{position:absolute;left:135px;top:306px;font-size:11px;font-weight:700}
.social{position:absolute;left:225px;top:298px;display:flex;gap:10px}
.social i{width:26px;height:26px;border-radius:50%;background:var(--sky);display:block}
.copyright{position:absolute;left:845px;top:308px;font-size:9.5px;text-transform:uppercase}
</style>
</head>
<body>
<div class="page">

<header class="site-header">
  <div class="brand"><span class="brand-dot"></span>QualiDial</div>
  <div class="call-us">
    <span class="call-icon"><svg width="16" height="16" viewBox="0 0 24 24"><path fill="#fff" d="M6.6 10.8a15 15 0 0 0 6.6 6.6l2.2-2.2c.3-.3.7-.4 1-.2 1.1.4 2.3.6 3.6.6.6 0 1 .4 1 1V20c0 .6-.4 1-1 1C10.6 21 3 13.4 3 4c0-.6.4-1 1-1h3.5c.6 0 1 .4 1 1 0 1.3.2 2.5.6 3.6.1.3 0 .7-.2 1z"/></svg></span>
    <div><small>CALL US NOW</small><strong>555.014.2290</strong></div>
  </div>
  <div class="search"><svg width="10" height="10" viewBox="0 0 24 24"><circle cx="10" cy="10" r="7" stroke="#555" stroke-width="3" fill="none"/><path d="M15 15l7 7" stroke="#555" stroke-width="3"/></svg>SEARCH</div>
  <nav class="main-nav">
    <span>Home</span><span>Services ▾</span><span class="active">System Details ▾</span><span>Sample Scorecards</span><span>Pricing</span><span>Team</span><span>Blog</span><span>Contact</span>
  </nav>
</header>

<section class="hero">
  <div class="hero-art" role="img" aria-label="Illustration of a call center agent with headset working at a laptop on a desk"></div>
  <div class="play" style="left:575px;top:160px;width:66px;height:66px"><svg width="26" height="26" viewBox="0 0 24 24"><path d="M6 3l15 9-15 9z" fill="#6b6f75"/></svg></div>
  <h1 class="hero-title">ACCURACY</h1>
</section>

<h2 class="section-title">ACCURACY</h2>
<div class="title-rule"></div>
<p class="intro">As part of our efforts in providing the highest level of accuracy when analyzing agent performance, we are continuously developing new and innovative methods to ensure our team is performing at their best. The following is a description of several processes we have in place to ensure our QA's are scoring as accurately as possible during their reviews.</p>

<div class="video" style="left:145px;top:823px;width:292px;height:193px">
  <div class="video-bar"><i style="background:#f25f57"></i><i style="background:#f8bd2e"></i><i style="background:#34c84a"></i></div>
  <div class="video-screen" role="img" aria-label="Screen recording of the calibration scoring table"></div>
  <div class="video-controls"></div>
  <div class="play" style="left:117px;top:67px"><svg width="22" height="22" viewBox="0 0 24 24"><path d="M6 3l15 9-15 9z" fill="#6b6f75"/></svg></div>
</div>
<h3 class="feature-title" style="left:565px;top:812px">Client Calibration Process</h3>
<p class="feature-text" style="left:565px;top:845px;width:500px">Client calibration is just one type of calibration method which requires both the client's supervisor(s) and QualiDial members to score a particular call. On QD's end, a QA, calibrator and Team Lead will review and score the call. Additionally, other users can also be added to this process as needed. At least one client supervisor will then score the same call which will be used as the baseline score. Once all relevant parties have finished reviewing / scoring the call, the results will appear side-by-side which allows for convenient score comparisons. In addition, client calibration is a perfect opportunity for the client and the QD team to discuss any variations in scoring as well as clear up any misunderstandings/uncertainties that may arise</p>

<h3 class="feature-title" style="left:140px;top:1121px;font-size:12px">Internal Calibration Process</h3>
<p class="feature-text" style="left:140px;top:1148px;width:485px">This calibration process provides an additional layer of quality which is done internally by QualiDial members and is typically set at 10% - 20% of all calls reviewed. QualiDial will determine the set percentage of calls to be calibrated daily based on scorecard complexity and other criteria. Once a record is scored by a QA, a QD calibrator then scores the record independently. This process is "blind" and the calibrator cannot see how the record was scored by the QA to ensure unbiased analysis. Once this process has been completed, the calibrator and Team Lead will discuss any errors in scoring made by the QA. This in turn is followed by an opportunity to coach the QA by the Team Lead when necessary.</p>
<div class="video" style="left:665px;top:1133px;width:362px;height:198px">
  <div class="video-bar"><i style="background:#f25f57"></i><i style="background:#f8bd2e"></i><i style="background:#34c84a"></i></div>
  <div class="video-screen" role="img" aria-label="Screen recording of the internal calibration record list"></div>
  <div class="video-controls"></div>
  <div class="play" style="left:152px;top:70px"><svg width="22" height="22" viewBox="0 0 24 24"><path d="M6 3l15 9-15 9z" fill="#6b6f75"/></svg></div>
</div>

<div class="video" style="left:155px;top:1450px;width:352px;height:192px">
  <div class="video-bar"><i style="background:#f25f57"></i><i style="background:#f8bd2e"></i><i style="background:#34c84a"></i></div>
  <div class="video-screen" role="img" aria-label="Screen recording of the recalibration review form"></div>
  <div class="video-controls"></div>
  <div class="play" style="left:147px;top:30px"><svg width="22" height="22" viewBox="0 0 24 24"><path d="M6 3l15 9-15 9z" fill="#6b6f75"/></svg></div>
</div>
<h3 class="feature-title" style="left:568px;top:1463px;font-size:12px">Recalibration Process</h3>
<p class="feature-text" style="left:568px;top:1500px;width:500px">The process of recalibration is essentially a way for us to calibrate our calibrators. As our reviews are done by humans, there will always be some level of inaccuracy. To combat this, QualiDial has begun implementing recalibrations which are designed to eliminate as much human error as possible and to ensure our calibrators remain accurate when calibrating calls. Recalibration is performed by a Team Lead who reviews the calibrator's scores on a daily basis for 10% of all the calls that have been calibrated internally.</p>

<h3 class="feature-title" style="left:140px;top:1755px">Disputes/Notification Process</h3>
<p class="feature-text" style="left:140px;top:1793px;width:345px">Disputes are activated by the client and done so when they disagree with the way a QA has scored a record. This does not happen automatically, rather it is instigated by the client by clicking the "create dispute" button at the bottom of the review_record page. Once the client creates a dispute, it follows a specific path back and forth between the client and QD team until the dispute is settled and an agreeable resolution is reached.</p>
<p class="feature-text" style="left:140px;top:1973px;width:345px">The Notification process utilizes the coaching queue module to manage calls which require attention for a variety of reasons. Whether due to a call failing, specific criteria having been missed on a call, or by way of the dispute process, the coaching queue module allows for client supervisors to review and act on calls which require attention or action.</p>
<div class="flow-panel" role="img" aria-label="Animated infographic of the dispute and notification workflow"></div>
<div class="play" style="left:770px;top:1884px"><svg width="22" height="22" viewBox="0 0 24 24"><path d="M6 3l15 9-15 9z" fill="#6b6f75"/></svg></div>

<div class="illustration" style="left:115px;top:2185px;width:408px;height:340px;background:linear-gradient(150deg,#e9eef2,#c9dce8)" role="img" aria-label="Isometric illustration of call center agents working in cubicles"></div>
<div class="play" style="left:290px;top:2325px"><svg width="22" height="22" viewBox="0 0 24 24"><path d="M6 3l15 9-15 9z" fill="#6b6f75"/></svg></div>
<h3 class="feature-title" style="left:607px;top:2240px">Spot Check Process</h3>
<p class="feature-text" style="left:607px;top:2280px;width:470px">The internal spot check process consists of 4 distinct features based on algorithms which generate spot check assignments for QD's Team Leads and Account Managers. This involves reviewing calls based on criteria such as QA call score, calibrated score, and calls which require additional review driven by question specific data. This process provides insight into areas where additional coaching is needed internally to ensure greater accuracy in analyzing agent performance. This most recent addition to QualiDial's quality control measures is intended to identify and address any remaining scoring errors not initially uncovered by the calibration/recalibration process.</p>

<h3 class="feature-title" style="left:140px;top:2682px">Historical Algorithms</h3>
<p class="feature-text" style="left:140px;top:2723px;width:470px">There are many variations of passages of Lorem Ipsum available, but the majority have suffered alteration in some form, by injected humour, or randomised words which don't look even slightly believable. If you are going to use a passage of Lorem Ipsum, you need to be sure there isn't anything embarrassing hidden in the middle of text. All the Lorem Ipsum generators on the Internet tend to repeat predefined chunks as necessary, making this the first true generator</p>
<div class="illustration" style="left:610px;top:2600px;width:432px;height:330px;background:linear-gradient(180deg,#ffffff,#eef1f3 55%,#d9dcdf)" role="img" aria-label="Illustration of a support agent at a laptop surrounded by clock, chat and 24-hour icons"></div>
<div class="play" style="left:800px;top:2770px"><svg width="22" height="22" viewBox="0 0 24 24"><path d="M6 3l15 9-15 9z" fill="#6b6f75"/></svg></div>

<footer class="site-footer">
  <div class="foot-head" style="left:135px;top:52px">Menu</div>
  <div class="foot-list" style="left:135px;top:78px">Home<br>Who We Are<br>Services<br>Blog<br>Login</div>
  <div class="foot-head" style="left:307px;top:52px">Contact Us</div>
  <div class="foot-contact" style="left:307px;top:80px">4410 Harbor Lane<br>Millbrook, CA 90210<br><br>HELLO@QUALIDIAL.EXAMPLE<br><br>555.014.2290</div>
  <div class="foot-head" style="left:550px;top:52px">Newsletter</div>
  <div class="email-field">E-MAIL ID</div>
  <div class="signup">SIGNUP</div>
  <div class="foot-brand"><span class="dot"></span>QualiDial</div>
  <div class="foot-rule"></div>
  <div class="follow">FOLLOW US</div>
  <div class="social"><i></i><i></i><i></i><i></i><i></i></div>
  <div class="copyright">© 2017 QualiDial. All rights reserved.</div>
</footer>

</div>
</body>
</html>
```